Local Flower Farm Needs Business Card Design

I need business cards designed for a flower farm based in Eudora, Kansas.
Business Info:
We are a local cut flower farm located in Eudora, Kansas, founded by Corinne Haldwick. What started as a passion for agriculture and search for more joy in daily life has blossomed into a small business dedicated to providing the community with beautiful, fresh, and sustainable flowers. We specialize in local, seasonal blooms, ensuring that every petal reflects the care and dedication we pour into our craft. Our mission is to deliver the highest quality flowers directly to our customers through local farmers markets and to florists who share our commitment to sustainability. Join us in celebrating the beauty of nature, one bloom at a time!
Contact Details:
Corinne Haldwick
Owner
Phone 913-555-0147
Facebook: Rosalind Thorpe Gardens
Instagram: @RosalindThorpeGardens
Website: RosalindThorpeGardens.example
Target Market(s)
Wholesale to Florists and Direct to Consumer via Farmers Market
Industry/Entity Type
Florist, Farm
Contact Information for Business Card
Name, Contact Info, Logo
Look and feel
Each slider illustrates characteristics of the customer's brand and the style your logo design should communicate.

```html
<!DOCTYPE html>
<html lang="en">
<head>
<meta charset="utf-8">
<title>Rosalind Thorpe Gardens – Business Card</title>
<link rel="stylesheet" href="https://fonts.googleapis.com/css2?family=Tinos:wght@400;700&display=swap">
<style>
  :root {
    --ink: #0b2730;
    --paper: #ffffff;
    --backdrop: #e4e8ea;
  }
  * { margin: 0; padding: 0; box-sizing: border-box; }
  html, body {
    width: 1200px; height: 960px; overflow: hidden;
    background: var(--backdrop);
    font-family: "Tinos", "Times New Roman", serif;
  }
  .card {
    position: absolute; left: 249px; width: 702px; height: 402px;
  }
  .card--front { top: 58px; background: var(--ink); color: var(--paper); }
  .card--back { top: 500px; background: var(--paper); color: var(--ink); }

  .brand-seal {
    position: absolute; border-radius: 50%;
    display: flex; align-items: center; justify-content: center;
    text-align: center; font-weight: 400; letter-spacing: 0.12em;
    text-transform: uppercase; line-height: 1.35;
  }
  .card--front .brand-seal {
    left: 219px; top: 66px; width: 270px; height: 270px;
    border: 1px solid var(--paper); font-size: 22px;
  }
  .card--back .brand-seal {
    left: 25px; top: 79px; width: 240px; height: 240px;
    border: 1px solid var(--ink); font-size: 19px;
  }

  .contact-rail { position: absolute; left: 0; top: 0; width: 702px; height: 402px; }

  .holder {
    position: absolute; right: 74px; top: 36px; text-align: right;
  }
  .holder__name { font-size: 34px; font-weight: 700; line-height: 1; letter-spacing: 0.01em; }
  .holder__role { font-size: 16px; margin-top: 3px; }

  .contact-list {
    position: absolute; right: 74px; top: 243px; list-style: none; text-align: right;
    font-size: 17px; letter-spacing: 0.02em;
  }
  .contact-list li { height: 30.5px; line-height: 22px; }
</style>
</head>
<body>

<section class="card card--front">
  <div class="brand-seal">Rosalind<br>Thorpe<br>Gardens</div>
</section>

<section class="card card--back">
  <div class="brand-seal">Rosalind<br>Thorpe<br>Gardens</div>

  <svg class="contact-rail" viewBox="0 0 702 402" aria-hidden="true">
    <line x1="658" y1="26" x2="658" y2="377" stroke="var(--ink)" stroke-width="2"/>
    <rect x="638" y="53" width="40" height="40" fill="var(--ink)" transform="rotate(45 658 73)"/>
    <g fill="var(--ink)">
      <rect x="649" y="247" width="18" height="18" transform="rotate(45 658 256)"/>
      <rect x="649" y="278" width="18" height="18" transform="rotate(45 658 287)"/>
      <rect x="649" y="309" width="18" height="18" transform="rotate(45 658 318)"/>
      <rect x="649" y="340" width="18" height="18" transform="rotate(45 658 349)"/>
    </g>
    <!-- phone -->
    <path d="M654.5 251.5 q-1.5 1 -0.5 3.5 q1.5 3.5 4.5 5 q2 1 3 -0.5 l-1.8 -1.6 q-0.8 0.6 -1.6 0 q-1.5 -1.2 -2 -2.3 q-0.4 -0.9 0.3 -1.4 z" fill="var(--paper)"/>
    <!-- plain marks for social rows -->
    <circle cx="658" cy="287" r="4" fill="none" stroke="var(--paper)" stroke-width="1.2"/>
    <circle cx="658" cy="318" r="4" fill="none" stroke="var(--paper)" stroke-width="1.2"/>
    <!-- globe -->
    <g fill="none" stroke="var(--paper)" stroke-width="1">
      <circle cx="658" cy="349" r="4.5"/>
      <ellipse cx="658" cy="349" rx="2" ry="4.5"/>
      <line x1="653.5" y1="349" x2="662.5" y2="349"/>
    </g>
  </svg>

  <div class="holder">
    <h1 class="holder__name">Corinne Haldwick</h1>
    <p class="holder__role">Owner</p>
  </div>

  <ul class="contact-list">
    <li>913-555-0147</li>
    <li>Rosalind Thorpe Gardens</li>
    <li>@RosalindThorpeGardens</li>
    <li>RosalindThorpeGardens.example</li>
  </ul>
</section>

</body>
</html>
```